Need App for Impact Related Events

My app is to help with internal events. When you enter the prompted event code the next screen shows you everyone currently at the event. It will give you the ability to Start a conversation with someone you met at that event, or signal it is your turn to send a message. The next screen is a message thread with that person. I am looking for a design that incorporates the colors and ‘feel good’ emotion of our logo. I have pieced together a pretty good interpretation of what I’m looking for in the attached mockup by slicing and dicing designs. I also attached our logo mascot.Screens (see attached mockups)

Note 1: I do not like the picture on the screen used in screen one because it makes it seem like a dating app. I attached an alternative photo that can be used or present different ideas.

Note 2: On the login/signup screen (screen 2) I need an additional first and last name for login, you can try to fit this on one login screen or present a two step signup screen where that is presented in the second screen.

READ MOCKUP GUIDELINES UNDER Must Haves

Target Market(s)

People attending internal social impact events

Industry/Entity Type

Charity

Font styles to use
Sans Serif

Colors
86cfc6

Requirements
Must have
• Follow the screen mockups attached to project
• PLEASE READ
• I have provided a relatively close design of what I’m looking for in the mockups. Some screens need to be followed more closely to my design mockup than other. I have listed a guide below how how closely you should follow my mockup design exactly. Overall I would like to see some ideas of incorporating a few accent colors so it doesn’t appear SO Blue. I also attached some app inspiration designs I found from around the web
• Screen Mockup Guideline Follow %
• Screen 1: 65% - mostly on target, would like to see ways to make it not SO Blue and possibly creative places to add some explainer text describing the app
• Screen 2: 50% - general design idea is here, but more open
• Screen 3: 35% - a lot more room for design influence
• Screen 4: 70% - mostly on target, a little room for design influence/color scheme ideas
• Screen 5-6: 25% - a lot of room for design change/ideas/influence
• Screen 7-8: 80% - already very close to what I need, maybe open to slight sizing and color scheme ideas
• Screen 9: 15% - the most open for influence, only the general functionality of the screen is communicated here
Nice to have
• Please Read Mockup Guideline above. In large part I am looking for something to use some nice accent colors so it is not overwhelmingly blue and bring the whole design into a seamless style.
Should not have

```html
<!DOCTYPE html>
<html lang="en">
<head>
<meta charset="utf-8">
<title>Who you've met – event chat screens</title>
<link href="https://fonts.googleapis.com/css2?family=Heebo:wght@300;400;500&display=swap" rel="stylesheet">
<style>
  :root{
    --accent:#2ee6c9;
    --accent-soft:#5ef0d8;
    --mint-bg:#eafbf8;
    --mint-wave:#d8f8f2;
    --ink:#2f3437;
    --ink-soft:#555b60;
    --muted:#8a9196;
    --divider:#dfe8e6;
    --bubble-in:#ededed;
    --kb-bg:#d3d6dc;
    --kb-key:#ffffff;
    --kb-key-dark:#acb1ba;
    --page:#ffffff;
    --avatar-a:#b9a08c;
    --avatar-b:#8d7565;
    --avatar-c:#c98a5e;
  }
  *{box-sizing:border-box;margin:0;padding:0}
  html,body{width:1200px;height:1200px;overflow:hidden}
  body{background:var(--page);font-family:"Heebo",sans-serif;color:var(--ink);position:relative}

  .screen{position:absolute;top:170px;width:400px;height:860px;border-radius:44px;overflow:hidden;
    box-shadow:0 0 0 1px #e3e7e7,0 18px 40px rgba(0,0,0,.08)}
  .screen--contacts{left:150px;background:linear-gradient(180deg,#f1fdfb 0%,var(--mint-bg) 60%,#f3fdfb 100%)}
  .screen--chat{left:650px;background:linear-gradient(180deg,#fbfefe 0%,#f0fcfa 100%)}

  .status-time{position:absolute;left:36px;top:16px;font-size:15px;font-weight:500;color:#111}
  .status-icons{position:absolute;right:28px;top:19px}

  .wave{position:absolute;left:0;top:90px;width:400px;height:200px}

  .topbar{position:absolute;left:0;top:50px;width:400px;height:42px}
  .back{position:absolute;left:18px;top:10px}
  .brand{position:absolute;left:118px;top:8px;display:flex;align-items:center;gap:8px}
  .brand-dot{width:22px;height:22px;border-radius:50%;background:var(--accent)}
  .brand-title{font-size:18px;font-weight:400;color:var(--ink)}
  .icon-search{position:absolute;left:318px;top:8px}
  .icon-gear{position:absolute;left:356px;top:7px}

  .contact-list{position:absolute;left:0;top:133px;width:400px;list-style:none}
  .contact{position:relative;height:80px;display:flex;align-items:center}
  .contact::after{content:"";position:absolute;left:30px;right:17px;bottom:0;height:1px;background:var(--divider)}
  .contact:last-child::after{display:block}
  .avatar{position:absolute;left:19px;width:52px;height:52px;border-radius:50%}
  .avatar--warm{background:radial-gradient(circle at 45% 40%,var(--avatar-a),var(--avatar-b))}
  .avatar--amber{background:radial-gradient(circle at 45% 40%,#e2b08c,var(--avatar-c))}
  .avatar--dark{background:radial-gradient(circle at 45% 40%,#9a8a80,#3d3533)}
  .contact-name{position:absolute;left:93px;font-size:19px;font-weight:300;color:var(--ink-soft);letter-spacing:-.2px}
  .action{position:absolute;right:14px;height:42px;border-radius:6px;background:var(--accent);
    color:#fff;font-size:18px;font-weight:300;display:flex;align-items:center;gap:6px;padding:0 14px 0 12px}

  .hidden-bar{position:absolute;left:19px;top:763px;width:364px;height:52px;border-radius:26px;
    background:linear-gradient(90deg,var(--accent) 0%,var(--accent-soft) 100%);
    box-shadow:0 6px 14px rgba(46,230,201,.28);display:flex;align-items:center;padding:0 20px;color:#fff}
  .hidden-label{margin-left:16px;font-size:19px;font-weight:400;flex:1}

  .chat-header{position:absolute;left:0;top:50px;width:400px;height:43px;border-bottom:1px solid var(--divider)}
  .chat-avatar{position:absolute;left:45px;top:4px;width:32px;height:32px;border-radius:50%;
    background:radial-gradient(circle at 45% 40%,var(--avatar-a),var(--avatar-b))}
  .chat-name{position:absolute;left:0;right:0;top:8px;text-align:center;font-size:19px;font-weight:400;color:var(--ink)}

  .timestamp{position:absolute;left:0;right:0;text-align:center;font-size:14px;font-weight:300;color:var(--muted)}
  .bubble{position:absolute;font-size:18px;font-weight:300;line-height:23px;padding:0 19px;display:flex;align-items:center}
  .bubble--in{left:19px;background:var(--bubble-in);color:var(--ink);border-radius:4px}
  .bubble--out{right:19px;background:var(--accent);color:#fff;border-radius:4px;justify-content:flex-end}
  .tail{position:absolute;width:0;height:0}
  .tail--in{left:0;bottom:-11px;border-left:14px solid var(--bubble-in);border-bottom:11px solid transparent}
  .tail--out{right:0;bottom:-11px;border-right:14px solid var(--accent);border-bottom:11px solid transparent}

  .composer{position:absolute;left:0;top:483px;width:400px;height:65px;border-top:1px solid var(--divider);background:#fbfefe}
  .composer-add{position:absolute;left:12px;top:14px}
  .composer-field{position:absolute;left:58px;top:12px;width:283px;height:40px;border:1px solid #e2e6e6;border-radius:20px;
    font-size:15px;font-weight:300;color:#b0b5b8;display:flex;align-items:center;padding-left:18px}
  .composer-field::before{content:"";width:1px;height:20px;background:#9aa0a4;margin-right:10px}
  .composer-send{position:absolute;left:348px;top:13px}

  .keyboard{position:absolute;left:0;top:548px;width:400px;height:312px;background:var(--kb-bg);padding:9px 5px 0}
  .kb-row{display:flex;justify-content:center;gap:6px;margin-bottom:13px}
  .key{width:33.5px;height:42px;border-radius:5px;background:var(--kb-key);box-shadow:0 1px 0 #888d95;
    display:flex;align-items:center;justify-content:center;font-size:23px;font-weight:300;color:#111}
  .key--dark{background:var(--kb-key-dark)}
  .key--wide{width:44px}
  .key--label{font-size:17px;font-weight:400}
  .kb-row--shift{justify-content:space-between;padding:0 0}
  .kb-letters{display:flex;gap:6px}
  .kb-extras{position:absolute;left:0;top:263px;width:400px}
  .kb-emoji{position:absolute;left:30px;top:0}
  .kb-mic{position:absolute;left:350px;top:0}
  .home-indicator{position:absolute;left:129px;top:294px;width:141px;height:5px;border-radius:3px;background:#111}
</style>
</head>
<body>

<section class="screen screen--contacts" aria-label="Who you've met list">
  <div class="status-time">9:41</div>
  <svg class="status-icons" width="50" height="14" viewBox="0 0 50 14">
    <path d="M2 5a11 11 0 0 1 14 0M4.5 7.5a7 7 0 0 1 9 0M7 10a3 3 0 0 1 4 0" stroke="#111" stroke-width="1.8" fill="none" stroke-linecap="round"/>
    <rect x="23" y="2" width="23" height="11" rx="3" fill="none" stroke="#111" stroke-width="1.2"/>
    <rect x="25" y="4" width="19" height="7" rx="1.5" fill="#111"/>
  </svg>

  <svg class="wave" viewBox="0 0 400 200" preserveAspectRatio="none">
    <path d="M0 40 C90 -5 200 10 270 60 C320 95 360 110 400 100 L400 200 L0 200Z" fill="var(--mint-wave)" opacity=".7"/>
  </svg>

  <header class="topbar">
    <svg class="back" width="14" height="24" viewBox="0 0 14 24"><path d="M12 2 2 12l10 10" stroke="#333" stroke-width="2.2" fill="none" stroke-linecap="round"/></svg>
    <div class="brand"><span class="brand-dot"></span><span class="brand-title">Who you’ve met</span></div>
    <svg class="icon-search" width="28" height="28" viewBox="0 0 28 28"><circle cx="12" cy="12" r="9" stroke="#333" stroke-width="2.4" fill="none"/><path d="M19 19l6 6" stroke="#333" stroke-width="2.6" stroke-linecap="round"/></svg>
    <svg class="icon-gear" width="28" height="28" viewBox="0 0 28 28"><circle cx="14" cy="14" r="10" fill="none" stroke="#333" stroke-width="5" stroke-dasharray="4 3.85"/><circle cx="14" cy="14" r="8" fill="#333"/><circle cx="14" cy="14" r="3.4" fill="#eefcf9"/></svg>
  </header>

  <ul class="contact-list">
    <li class="contact">
      <span class="avatar avatar--warm" role="img" aria-label="Profile photo of Marco Vale"></span>
      <span class="contact-name">Marco Vale</span>
      <span class="action"><svg width="24" height="24" viewBox="0 0 24 24"><path d="M4 22V3M4 4h10l-1.5 3L14 10H4" stroke="#fff" stroke-width="1.6" fill="none"/><path d="M14 5h6l-1.5 3 1.5 3h-7" stroke="#fff" stroke-width="1.6" fill="none"/></svg>Start</span>
    </li>
    <li class="contact">
      <span class="avatar avatar--amber" role="img" aria-label="Profile photo of Nina Ford"></span>
      <span class="contact-name">Nina Ford</span>
      <span class="action"><svg width="24" height="24" viewBox="0 0 24 24"><path d="M4 22V3M4 4h10l-1.5 3L14 10H4" stroke="#fff" stroke-width="1.6" fill="none"/><path d="M14 5h6l-1.5 3 1.5 3h-7" stroke="#fff" stroke-width="1.6" fill="none"/></svg>Start</span>
    </li>
    <li class="contact">
      <span class="avatar avatar--amber" role="img" aria-label="Profile photo of Ivy Dorsey"></span>
      <span class="contact-name">Ivy Dorsey</span>
      <span class="action"><svg width="22" height="24" viewBox="0 0 22 24"><path d="M4 23V5h12M12 1l4 4-4 4" stroke="#fff" stroke-width="1.6" fill="none"/></svg>Your Turn</span>
    </li>
    <li class="contact">
      <span class="avatar avatar--dark" role="img" aria-label="Profile photo of Carla Wendt"></span>
      <span class="contact-name">Carla Wendt</span>
    </li>
    <li class="contact">
      <span class="avatar avatar--dark" role="img" aria-label="Profile photo of Owen Marsh"></span>
      <span class="contact-name">Owen Marsh</span>
    </li>
    <li class="contact">
      <span class="avatar avatar--warm" role="img" aria-label="Profile photo of Luis Ocampo"></span>
      <span class="contact-name">Luis Ocampo</span>
    </li>
    <li class="contact">
      <span class="avatar avatar--dark" role="img" aria-label="Profile photo of Tessa Blake"></span>
      <span class="contact-name">Tessa Blake</span>
    </li>
  </ul>

  <div class="hidden-bar">
    <svg width="30" height="22" viewBox="0 0 30 22"><path d="M2 11c4-6 9-8 13-8s9 2 13 8c-4 6-9 8-13 8S6 17 2 11Z" stroke="#fff" stroke-width="2.2" fill="none"/><circle cx="15" cy="11" r="4" fill="#fff"/><path d="M6 20 24 2" stroke="#fff" stroke-width="2.4" stroke-linecap="round"/></svg>
    <span class="hidden-label">Hidden (52)</span>
    <svg width="26" height="16" viewBox="0 0 26 16"><path d="M2 3l11 10L24 3" stroke="#fff" stroke-width="2.6" fill="none" stroke-linecap="round"/></svg>
  </div>
</section>

<section class="screen screen--chat" aria-label="Message thread with Marco Vale">
  <div class="status-time">9:41</div>
  <svg class="status-icons" width="50" height="14" viewBox="0 0 50 14">
    <path d="M2 5a11 11 0 0 1 14 0M4.5 7.5a7 7 0 0 1 9 0M7 10a3 3 0 0 1 4 0" stroke="#111" stroke-width="1.8" fill="none" stroke-linecap="round"/>
    <rect x="23" y="2" width="23" height="11" rx="3" fill="none" stroke="#111" stroke-width="1.2"/>
    <rect x="25" y="4" width="19" height="7" rx="1.5" fill="#111"/>
  </svg>

  <header class="chat-header">
    <svg class="back" width="14" height="24" viewBox="0 0 14 24"><path d="M12 2 2 12l10 10" stroke="#333" stroke-width="2.2" fill="none" stroke-linecap="round"/></svg>
    <span class="chat-avatar" role="img" aria-label="Profile photo of Marco Vale"></span>
    <h1 class="chat-name">Marco Vale</h1>
  </header>

  <p class="timestamp" style="top:104px">Today at 5:03 PM</p>
  <div class="bubble bubble--in" style="top:142px;width:203px;height:52px">Hey! How’s it going?</div>
  <div class="bubble bubble--in" style="top:203px;width:264px;height:71px">Would you like to go the coffee tonight?<span class="tail tail--in"></span></div>

  <p class="timestamp" style="top:304px">5:33 PM</p>
  <div class="bubble bubble--out" style="top:343px;width:117px;height:51px">OK, sure !</div>
  <div class="bubble bubble--out" style="top:402px;width:224px;height:51px">When do you want to go?<span class="tail tail--out"></span></div>

  <div class="composer">
    <svg class="composer-add" width="34" height="34" viewBox="0 0 34 34"><circle cx="17" cy="17" r="15" stroke="var(--accent)" stroke-width="2" fill="none"/><path d="M17 9v16M9 17h16" stroke="var(--accent)" stroke-width="2"/></svg>
    <div class="composer-field">Type a message...</div>
    <svg class="composer-send" width="38" height="34" viewBox="0 0 38 34"><path d="M2 15 36 2 24 32 17 19Z" fill="var(--accent)"/><path d="M17 19 36 2" stroke="#fff" stroke-width="1.5"/></svg>
  </div>

  <div class="keyboard">
    <div class="kb-row">
      <span class="key">q</span><span class="key">w</span><span class="key">e</span><span class="key">r</span><span class="key">t</span><span class="key">y</span><span class="key">u</span><span class="key">i</span><span class="key">o</span><span class="key">p</span>
    </div>
    <div class="kb-row">
      <span class="key">a</span><span class="key">s</span><span class="key">d</span><span class="key">f</span><span class="key">g</span><span class="key">h</span><span class="key">j</span><span class="key">k</span><span class="key">l</span>
    </div>
    <div class="kb-row kb-row--shift">
      <span class="key key--dark key--wide"><svg width="20" height="20" viewBox="0 0 20 20"><path d="M10 2 2 10h4v7h8v-7h4Z" stroke="#111" stroke-width="1.4" fill="none" stroke-linejoin="round"/></svg></span>
      <span class="kb-letters"><span class="key">z</span><span class="key">x</span><span class="key">c</span><span class="key">v</span><span class="key">b</span><span class="key">n</span><span class="key">m</span></span>
      <span class="key key--dark key--wide"><svg width="26" height="18" viewBox="0 0 26 18"><path d="M8 1h16v16H8L1 9Z" stroke="#111" stroke-width="1.4" fill="none" stroke-linejoin="round"/><path d="M12 5l8 8M20 5l-8 8" stroke="#111" stroke-width="1.4"/></svg></span>
    </div>
    <div class="kb-row">
      <span class="key key--dark key--label" style="width:90px">123</span>
      <span class="key key--label" style="width:94px">space</span>
      <span class="key" style="width:43px">@</span>
      <span class="key" style="width:43px">.</span>
      <span class="key key--dark key--label" style="width:91px">return</span>
    </div>
    <div class="kb-extras">
      <svg class="kb-emoji" width="30" height="30" viewBox="0 0 30 30"><circle cx="15" cy="15" r="13" stroke="#555" stroke-width="1.6" fill="none"/><circle cx="10.5" cy="12" r="1.6" fill="#555"/><circle cx="19.5" cy="12" r="1.6" fill="#555"/><path d="M8 17c2 5 12 5 14 0Z" fill="#555"/></svg>
      <svg class="kb-mic" width="20" height="32" viewBox="0 0 20 32"><rect x="5" y="2" width="10" height="18" rx="5" stroke="#555" stroke-width="1.6" fill="none"/><path d="M2 15a8 8 0 0 0 16 0M10 23v7" stroke="#555" stroke-width="1.6" fill="none"/></svg>
    </div>
    <div class="home-indicator"></div>
  </div>
</section>

</body>
</html>
```